Business card for my new company (Accounting firm)

I need a business card for my new business Brightwell Advisory and Ledger SA. Our services are accounting, tax, audit and financial management. Our customers are small companies, start-ups and new companies. The final design has to show financial security, trust and growth. Please find our logo attached to the business card. Text for the business card: Brightwell Advisory and Ledger SA Tomas Varenholt Director and Founder Certified Accountant Tel. 022 418 57 34 tv@clairevalconseil.ch www.clairevalconseil.ch Rue des Vergières 27 1201 Geneva
Target Market(s)
Our customers are small companies, start-ups and new companies.
Industry/Entity Type
Finance And Accounting
Contact Information for Business Card
Claireval Conseil et Comptes SA
Tomas Varenholt
Directeur et Fondateur
Expert-comptable diplômé
Tél. 022 418 57 34
tv@clairevalconseil.ch
www.clairevalconseil.ch
Rue des Vergières 27
1201 Genève

```html
<!DOCTYPE html>
<html lang="en">
<head>
<meta charset="utf-8">
<title>Claireval Conseil et Comptes SA – Business Card</title>
<link href="https://fonts.googleapis.com/css2?family=Lato:wght@400;700&display=swap" rel="stylesheet">
<style>
  :root {
    --stage: #8b4c22;
    --blue-top: #2188c8;
    --blue-mid: #34aee2;
    --blue-bottom: #2170a8;
    --white: #ffffff;
    --rule: rgba(255,255,255,0.75);
    --ink-dark: #38393b;
    --brand-blue: #2a8ac8;
    --card-shadow: 2px 3px 6px rgba(0,0,0,0.45);
  }
  * { margin: 0; padding: 0; box-sizing: border-box; }
  html, body { width: 1200px; height: 900px; overflow: hidden; }
  body {
    position: relative;
    background: var(--stage);
    font-family: 'Lato', sans-serif;
  }
  .card {
    position: absolute;
    box-shadow: var(--card-shadow);
  }
  .card-front {
    left: 330px; top: 90px; width: 555px; height: 343px;
    background: linear-gradient(to bottom, var(--blue-top) 0%, var(--blue-mid) 55%, var(--blue-bottom) 100%);
    color: var(--white);
    text-align: center;
  }
  .holder-name {
    position: absolute; left: 0; right: 0; top: 62px;
    font-size: 18px; font-weight: 700; letter-spacing: 0.2px;
  }
  .holder-role {
    position: absolute; left: 0; right: 0; top: 84px;
    font-size: 16px; line-height: 19.5px;
  }
  .icon-row {
    position: absolute; left: 188px; top: 132px; width: 178px; height: 24px;
  }
  .contact-list {
    position: absolute; left: 0; right: 0; top: 163px;
    font-size: 16px; line-height: 20px; list-style: none;
  }
  .divider {
    position: absolute; left: 188px; top: 232px; width: 178px; height: 1px;
    background: var(--rule);
  }
  .address {
    position: absolute; left: 0; right: 0; top: 242px;
    font-size: 16px; line-height: 20px; font-style: normal;
  }
  .card-back {
    left: 330px; top: 469px; width: 559px; height: 343px;
    background: var(--white);
  }
  .brand-mark {
    position: absolute; left: 250px; top: 92px; width: 60px; height: 60px;
    background: var(--brand-blue);
  }
  .brand-name {
    position: absolute; left: 0; right: 0; top: 200px;
    text-align: center; color: var(--ink-dark); font-weight: 700;
  }
  .brand-name .primary { display: block; font-size: 40px; letter-spacing: 3px; line-height: 44px; }
  .brand-name .secondary { display: block; font-size: 13px; letter-spacing: 2.2px; line-height: 18px; }
</style>
</head>
<body>
  <section class="card card-front">
    <h1 class="holder-name">SA TOMAS VARENHOLT</h1>
    <p class="holder-role">Director and Founder<br>Certified Accountant</p>
    <svg class="icon-row" viewBox="0 0 178 24" aria-hidden="true">
      <line x1="0" y1="12" x2="50" y2="12" stroke="rgba(255,255,255,0.75)" stroke-width="1"/>
      <line x1="128" y1="12" x2="178" y2="12" stroke="rgba(255,255,255,0.75)" stroke-width="1"/>
      <circle cx="63" cy="12" r="11" fill="#fff"/>
      <path d="M56 15 q0-6 7-6 q7 0 7 6 z M59 15 h8 v2 h-8z" fill="#2a9ad6"/>
      <circle cx="89" cy="12" r="11" fill="#fff"/>
      <rect x="82" y="7.5" width="14" height="9" fill="none" stroke="#2a9ad6" stroke-width="1.8"/>
      <path d="M82 8 l7 5 l7-5" fill="none" stroke="#2a9ad6" stroke-width="1.6"/>
      <circle cx="115" cy="12" r="11" fill="#fff"/>
      <circle cx="115" cy="12" r="6.5" fill="none" stroke="#2a9ad6" stroke-width="1.8"/>
      <path d="M108.5 12 h13 M115 5.5 q-4 6.5 0 13 q4-6.5 0-13" fill="none" stroke="#2a9ad6" stroke-width="1.3"/>
    </svg>
    <ul class="contact-list">
      <li>022 418 57 34</li>
      <li>tv@clairevalconseil.ch</li>
      <li>www.clairevalconseil.ch</li>
    </ul>
    <div class="divider"></div>
    <address class="address">Rue des Vergières 27<br>1201 Geneva</address>
  </section>

  <section class="card card-back">
    <div class="brand-mark"></div>
    <p class="brand-name">
      <span class="primary">CLAIREVAL</span>
      <span class="secondary">CONSEIL ET COMPTES</span>
    </p>
  </section>
</body>
</html>
```